Fenwick Grading LTD - website for irrigation & Landscape Lighting & Buried service wire

Looking for a website to help promote my business with Irrigation (installation, service, etc) and buried service wire/drainage solutions.

Commercial/Residential

Landscape lighting.

I’ll get photos in the trucks and trailers to upload as well maybe the machine as well.

Target Market(s)

Homeowners who want green grass and beautiful gardens. Beautiful landscape lighting

Industry/Entity Type

Irrigation systems and landscape lighting and buried service wire to homes and offering Drainage soltions.

Coding

Coded - Design and coding required

Number of Pages Required

4 page

Colors
F0912C
F2A743
F7CA91
FBE8D2
FDF5EE

Requirements
Must have
• was hoping to link up my email on fenwickgrading@mailbox-example.net with the website if possible.
Nice to have
• Page for Irrigation, page for landscape lighting, page buried service wire & drainage soltions.

```html
<!DOCTYPE html>
<html lang="en">
<head>
<meta charset="utf-8">
<title>Fenwick Grading LTD</title>
<link rel="stylesheet" href="https://fonts.googleapis.com/css2?family=Poppins:wght@400;500;600;700;800&display=swap">
<style>
:root{
  --orange:#F0912C;
  --orange-2:#F2A743;
  --orange-3:#F7CA91;
  --cream:#FBE8D2;
  --cream-2:#FDF5EE;
  --ink:#2b2b2b;
  --text:#4a4a4a;
  --dark:#1e1e1e;
  --white:#ffffff;
}
*{margin:0;padding:0;box-sizing:border-box}
html,body{width:1200px;height:3265px;overflow:hidden;background:var(--white)}
body{font-family:'Poppins',sans-serif;color:var(--text);position:relative}
.abs{position:absolute}
a{color:inherit;text-decoration:none}

/* header */
.site-header{position:absolute;left:0;top:0;width:1200px;height:124px;background:var(--white)}
.brand{position:absolute;left:75px;top:40px;width:190px;display:flex;align-items:center;gap:10px}
.brand-mark{width:28px;height:28px;border-radius:50%;background:var(--orange);flex:none}
.brand-name{font-weight:700;font-size:19px;line-height:22px;color:var(--orange);text-transform:uppercase}
.top-contact{position:absolute;right:73px;top:26px;display:flex;align-items:center;gap:22px;font-size:16px;color:var(--orange);font-weight:500}
.top-contact .item{display:flex;align-items:center;gap:14px}
.icon-circle{width:34px;height:34px;border-radius:50%;background:var(--ink);display:flex;align-items:center;justify-content:center}
.main-nav{position:absolute;right:73px;top:91px;display:flex;gap:31px;font-size:12.5px;font-weight:600;color:var(--ink);text-transform:uppercase}
.main-nav .active{color:var(--orange)}

/* hero */
.hero{position:absolute;left:0;top:124px;width:1200px;height:594px}
.hero-box{position:absolute;left:75px;top:265px;width:449px;height:238px;background:rgba(20,20,14,.82);padding:16px 18px}
.hero-box h1{font-size:40px;line-height:44px;font-weight:800;color:var(--white);text-transform:uppercase}
.hero-box h1 span{color:var(--orange)}
.hero-box p{font-size:20px;line-height:27px;color:var(--white);margin-top:6px}
.hero-buttons{display:flex;gap:8px;margin-top:12px}
.btn-solid{background:var(--orange);color:var(--white);font-size:12.5px;font-weight:700;height:43px;width:124px;display:flex;align-items:center;justify-content:center;text-transform:uppercase}
.btn-ghost{border:2px solid var(--white);color:var(--white);font-size:12.5px;font-weight:700;height:43px;width:124px;display:flex;align-items:center;justify-content:center;gap:8px;text-transform:uppercase}
.dots{position:absolute;left:565px;top:645px;display:flex;gap:11px}
.dots i{width:10px;height:10px;border-radius:50%;background:var(--white)}
.dots i.on{background:var(--orange)}

/* services */
.section-title{position:absolute;left:0;width:1200px;text-align:center;font-size:39px;font-weight:700;color:var(--ink);text-transform:uppercase}
.service-card{position:absolute;top:846px;width:329px;height:437px;background:var(--white);border-radius:12px;box-shadow:0 4px 18px rgba(0,0,0,.12);text-align:center}
.service-photo{height:232px;border-radius:12px 12px 0 0}
.service-card h3{font-size:19px;line-height:28px;font-weight:700;color:var(--orange);text-transform:uppercase;margin:18px 30px 0}
.service-card p{font-size:13.5px;line-height:22.5px;color:var(--text);margin:8px 28px 0}
.btn-dark{position:absolute;left:102px;bottom:-20px;width:124px;height:42px;background:var(--dark);color:var(--white);font-size:12.5px;font-weight:700;display:flex;align-items:center;justify-content:center;text-transform:uppercase}
.slider-arrow{position:absolute;top:1048px}

/* split */
.split{position:absolute;left:0;top:1375px;width:1200px;height:522px}
.split-panel{position:absolute;top:0;width:600px;height:522px;text-align:center;color:var(--white)}
.split-panel h2{margin-top:145px;font-size:41px;font-weight:700;text-transform:uppercase}
.split-panel p{font-size:14.5px;line-height:26.5px;margin:12px 40px 0}
.btn-outline-white{display:inline-flex;margin-top:26px;width:178px;height:53px;border:2px solid var(--white);align-items:center;justify-content:center;font-size:15.5px;font-weight:700;text-transform:uppercase}

/* feature rows */
.feature-photo{position:absolute}
.feature-text{position:absolute;background:var(--white)}
.feature-text h2{font-size:26px;line-height:30.5px;font-weight:700;color:var(--ink);text-transform:uppercase}
.feature-text p{font-size:15px;line-height:24.5px;color:var(--text);margin-top:16px}
.btn-outline-orange{display:flex;margin-top:26px;width:179px;height:53px;border:2px solid var(--orange);color:var(--orange);align-items:center;justify-content:center;font-size:15.5px;font-weight:700;text-transform:uppercase}

/* footer */
.site-footer{position:absolute;left:0;top:2913px;width:1200px;height:352px}
.footer-col{position:absolute;top:126px;color:var(--white)}
.footer-col h4{font-size:17.5px;font-weight:700;text-transform:uppercase;margin-bottom:10px}
.footer-col li{list-style:none;font-size:14px;line-height:31px}
.contact-row{display:flex;gap:14px;font-size:14px;line-height:23px;margin-bottom:14px}
.contact-row svg{flex:none;margin-top:5px}
.footer-brand{position:absolute;left:450px;top:95px;width:300px;text-align:center;color:var(--white)}
.footer-brand .brand-name{font-size:24px;line-height:28px}
.footer-brand .copy{font-size:12.5px;line-height:21px;margin-top:26px}
.socials{display:flex;justify-content:center;gap:16px;margin-top:16px}
.socials i{width:20px;height:20px;border-radius:50%;border:2px solid var(--white)}
</style>
</head>
<body>

<header class="site-header">
  <div class="brand"><span class="brand-mark"></span><span class="brand-name">Fenwick Grading LTD</span></div>
  <div class="top-contact">
    <div class="item">
      <span class="icon-circle"><svg width="16" height="16" viewBox="0 0 24 24"><path fill="#fff" d="M6.6 10.8a15 15 0 0 0 6.6 6.6l2.2-2.2c.3-.3.7-.4 1-.2 1.1.4 2.3.6 3.6.6.6 0 1 .4 1 1V20c0 .6-.4 1-1 1A17 17 0 0 1 3 4c0-.6.4-1 1-1h3.5c.6 0 1 .4 1 1 0 1.3.2 2.5.6 3.6.1.3 0 .7-.2 1z"/></svg></span>
      <span>1-800-555-0142</span>
    </div>
    <div class="item">
      <span class="icon-circle"><svg width="16" height="14" viewBox="0 0 24 20"><path fill="#fff" d="M2 2h20v16H2z"/><path fill="none" stroke="#2b2b2b" stroke-width="2" d="M2 3l10 8 10-8"/></svg></span>
      <span>fenwickgrading@mailbox-example.net</span>
    </div>
  </div>
  <nav class="main-nav">
    <a class="active">Home</a><a>Irrigation Services</a><a>Landscape Lighting</a><a>Fiber Optic Installation</a><a>Contact Us</a>
  </nav>
</header>

<section class="hero">
  <svg class="abs" style="left:0;top:0" width="1200" height="594" role="img" aria-label="Lawn sprinkler spraying water over a sunlit green lawn">
    <defs>
      <linearGradient id="heroGrad" x1="0" y1="0" x2="0" y2="1">
        <stop offset="0" stop-color="#4d5a3a"/>
        <stop offset=".45" stop-color="#6f8a3e"/>
        <stop offset="1" stop-color="#3f6b22"/>
      </linearGradient>
      <radialGradient id="heroGlow" cx=".65" cy=".35" r=".45">
        <stop offset="0" stop-color="#c9d98a" stop-opacity=".7"/>
        <stop offset="1" stop-color="#c9d98a" stop-opacity="0"/>
      </radialGradient>
    </defs>
    <polygon points="0,0 1200,0 1200,510 600,594 0,510" fill="url(#heroGrad)"/>
    <polygon points="0,0 1200,0 1200,510 600,594 0,510" fill="url(#heroGlow)"/>
  </svg>
  <div class="hero-box">
    <h1>Welcome to<br><span>Fenwick</span> Grading</h1>
    <p>Excepteur sint occaecat cupidatat non proident, sunt in culpa qui</p>
    <div class="hero-buttons">
      <span class="btn-solid">Read More</span>
      <span class="btn-ghost"><svg width="15" height="15" viewBox="0 0 16 16"><circle cx="8" cy="8" r="7" fill="none" stroke="#fff" stroke-width="1.6"/><path d="M6 4.8v6.4L11 8z" fill="#fff"/></svg>Play Video</span>
    </div>
  </div>
  <div class="dots"><i class="on"></i><i></i><i></i><i></i></div>
</section>

<h2 class="section-title" style="top:768px">Our Services</h2>

<svg class="slider-arrow" style="left:38px" width="24" height="34" viewBox="0 0 24 34"><path d="M20 2L4 17l16 15" fill="none" stroke="#777" stroke-width="2.5"/></svg>
<svg class="slider-arrow" style="left:1138px" width="24" height="34" viewBox="0 0 24 34"><path d="M4 2l16 15L4 32" fill="none" stroke="#777" stroke-width="2.5"/></svg>

<article class="service-card" style="left:75px">
  <div class="service-photo" role="img" aria-label="Technician installing irrigation controller in a garden" style="background:linear-gradient(160deg,#5c6b3a,#4f8a3c 55%,#2f6e2a)"></div>
  <h3>Irrigation Installs Service</h3>
  <p>Sed ut perspiciatis unde omnis iste natus error sit voluptatemaccusantium doloremque laudantium, totam rem aperiam, eaque ipsa quae.</p>
  <span class="btn-dark">Read More</span>
</article>
<article class="service-card" style="left:436px">
  <div class="service-photo" role="img" aria-label="Lit garden pathway leading to a house at dusk" style="background:linear-gradient(170deg,#2c3a3a,#3c4a34 50%,#a49a78 85%,#5b6b3e)"></div>
  <h3>Landscape Lighting</h3>
  <p>Sed ut perspiciatis unde omnis iste natus error sit voluptatemaccusantium doloremque laudantium, totam rem aperiam, eaque ipsa quae.</p>
  <span class="btn-dark">Read More</span>
</article>
<article class="service-card" style="left:797px">
  <div class="service-photo" role="img" aria-label="Bundled conduit and buried service wire in a trench" style="background:linear-gradient(160deg,#b8b6ae,#6a6a66 45%,#3a3a38 80%,#a8a59c)"></div>
  <h3>Buried Service Wire &amp; Drainage Solutions</h3>
  <p>Sed ut perspiciatis unde omnis iste natus error sit voluptatemaccusantium doloremque laudantium, totam rem aperiam, eaque ipsa quae.</p>
  <span class="btn-dark">Read More</span>
</article>

<section class="split">
  <svg class="abs" style="left:0;top:0" width="1200" height="522">
    <defs>
      <linearGradient id="resGrad" x1="0" y1="0" x2="1" y2="1">
        <stop offset="0" stop-color="#e9932f"/><stop offset="1" stop-color="#cf7a22"/>
      </linearGradient>
      <linearGradient id="comGrad" x1="0" y1="0" x2="0" y2="1">
        <stop offset="0" stop-color="#55606a"/><stop offset=".6" stop-color="#6b706c"/><stop offset="1" stop-color="#5b6a48"/>
      </linearGradient>
    </defs>
    <polygon role="img" aria-label="Suburban family home with orange overlay" points="0,0 602,37 602,485 0,522" fill="url(#resGrad)"/>
    <polygon role="img" aria-label="Modern commercial building with landscaped lawn" points="602,37 1200,0 1200,522 602,485" fill="url(#comGrad)"/>
  </svg>
  <div class="split-panel" style="left:24px;width:600px">
    <h2>Residential</h2>
    <p>Sed ut perspiciatis unde omnis iste natus error sit voluptatem accusantium doloremque laudantium, totam rem aperiam, eaque ipsa quae ab illo inventore veritatis et quasi architecto.</p>
    <span class="btn-outline-white">Read More</span>
  </div>
  <div class="split-panel" style="left:594px;width:600px">
    <h2>Commercial</h2>
    <p>Sed ut perspiciatis unde omnis iste natus error sit voluptatem accusantium doloremque laudantium, totam rem aperiam, eaque ipsa quae ab illo inventore veritatis et quasi architecto.</p>
    <span class="btn-outline-white">Read More</span>
  </div>
</section>

<div class="feature-photo" role="img" aria-label="Family playing football on a green lawn" style="left:75px;top:1953px;width:599px;height:414px;background:linear-gradient(170deg,#5f7d3c,#8aa85a 45%,#6d9a35 70%,#4d7f24)"></div>
<div class="feature-text" style="left:586px;top:2005px;width:541px;height:312px;padding:30px 0 0 29px">
  <h2>Homeowners who want green grass &amp; beautiful gardens. Beautiful landscape lighting</h2>
  <p>Sed ut perspiciatis unde omnis iste natus error sit voluptatem accusantium doloremque laudantium, totam rem aperiam, eaque ipsa quae ab illo inventore veritatis.</p>
  <span class="btn-outline-orange">Read More</span>
</div>

<div class="feature-photo" role="img" aria-label="Sprinkler watering a lush lawn beside flower beds" style="left:526px;top:2432px;width:600px;height:414px;background:linear-gradient(165deg,#3e4c36,#5d7a3a 45%,#78a23c 75%,#4f7d28)"></div>
<div class="feature-text" style="left:40px;top:2482px;width:574px;height:313px;padding:40px 0 0 35px">
  <h2>Irrigation systems &amp; landscape lighting and fiber optic installation to homes</h2>
  <p style="padding-right:40px">Sed ut perspiciatis unde omnis iste natus error sit voluptatem accusantium doloremque laudantium, totam rem aperiam, eaque ipsa quae ab illo inventore veritatis.</p>
  <span class="btn-outline-orange">Read More</span>
</div>

<footer class="site-footer">
  <svg class="abs" style="left:0;top:0" width="1200" height="352"><polygon points="0,84 600,0 1200,84 1200,352 0,352" fill="var(--dark)"/></svg>
  <div class="footer-col" style="left:250px">
    <h4>Site Map</h4>
    <ul><li>Home</li><li>Irrigation Services</li><li>Landscape Lighting</li><li>Fiber Optic Installation</li><li>Contact Us</li></ul>
  </div>
  <div class="footer-brand">
    <div style="display:flex;justify-content:center;align-items:center;gap:10px"><span class="brand-mark"></span><span class="brand-name">Fenwick Grading LTD</span></div>
    <div class="copy">Copyright © 2024. Company Name.<br>All Right Reserved</div>
    <div class="socials"><i></i><i></i><i></i><i></i><i></i></div>
  </div>
  <div class="footer-col" style="left:797px">
    <h4>Contact Info</h4>
    <div class="contact-row"><svg width="14" height="12" viewBox="0 0 14 12"><path d="M0 1l4.5-1 5 1.5L14 0v11l-4.5 1-5-1.5L0 12z" fill="var(--orange)"/></svg><span>48 Orchard Lane Unit 12,<br>Barrie ON L4M 0A1, Canada</span></div>
    <div class="contact-row"><svg width="12" height="12" viewBox="0 0 24 24"><path fill="var(--orange)" d="M6.6 10.8a15 15 0 0 0 6.6 6.6l2.2-2.2c.3-.3.7-.4 1-.2 1.1.4 2.3.6 3.6.6.6 0 1 .4 1 1V20c0 .6-.4 1-1 1A17 17 0 0 1 3 4c0-.6.4-1 1-1h3.5c.6 0 1 .4 1 1 0 1.3.2 2.5.6 3.6.1.3 0 .7-.2 1z"/></svg><span>+1-800-555-0142</span></div>
    <div class="contact-row"><svg width="14" height="11" viewBox="0 0 24 20"><path fill="var(--orange)" d="M2 2h20v16H2z"/><path fill="none" stroke="#1e1e1e" stroke-width="2" d="M2 3l10 8 10-8"/></svg><span>fenwickgrading@mailbox-example.net</span></div>
  </div>
</footer>

</body>
</html>
```